Banner ads for LP that work with same theme as below banners

Love the banner ads below. Need more with attached photos. But use the same wording, font as in below banner ads. Should be LP size 1200/627 so I can use for Pixorly and LP. Looking for great ads to use as LP ads. We do lots of ads so it will be worth your time to enter this contest you will be rewarded with a ton of work. Need several banner ads that work together. So maybe 1 of the dresses, 1 of the sweater, 1 of the leggings, 1 of the jacket

Target Market(s)

Women 24-45

Industry/Entity Type

Fashion

Requirements
Must have
• Banner ads that work for LP and Pixorly
Nice to have
• Several options to choose from
Should not have
• not sure

```html
<!DOCTYPE html>
<html lang="en">
<head>
<meta charset="utf-8">
<title>Our Best Dresses Ever! — Shop the Look</title>
<link rel="stylesheet" href="https://fonts.googleapis.com/css2?family=Parisienne&family=Playfair+Display:wght@400;700&family=Tinos:wght@700&display=swap">
<style>
  :root {
    --canvas: #ffffff;
    --band-grey: #c7c4bf;
    --panel-grey: #cecac5;
    --bronze: #7b5a2d;
    --bronze-dark: #5e4220;
    --ink: #1a1a1a;
    --headline-grey: #4c4c4c;
    --button-dark: #3d3f43;
    --button-edge: #6a6c70;
    --button-text: #f3f3f3;
    --frame-white: #ffffff;
    --frame-edge: #c9c9c9;
  }
  * { box-sizing: border-box; margin: 0; padding: 0; }
  html, body { width: 1200px; height: 627px; overflow: hidden; background: var(--canvas); }
  .banner {
    position: relative;
    width: 1200px;
    height: 627px;
    overflow: hidden;
    background: var(--canvas);
  }
  .backdrop { position: absolute; inset: 0; }
  .photo-card {
    position: absolute;
    left: 120px;
    top: 200px;
    width: 500px;
    height: 500px;
    transform: rotate(-24deg);
    background: var(--frame-white);
    border: 6px solid var(--frame-edge);
    box-shadow: 0 6px 18px rgba(0,0,0,0.25);
    padding: 14px;
  }
  .photo-card__image {
    width: 100%;
    height: 100%;
    background: linear-gradient(160deg, #e9dccf 0%, #b98a5c 30%, #3b2d2a 58%, #2e4f86 80%, #1f1a1c 100%);
  }
  .headline {
    position: absolute;
    left: 600px;
    top: 40px;
    width: 450px;
    text-align: center;
    color: var(--ink);
  }
  .headline__lead {
    display: block;
    font-family: "Parisienne", cursive;
    font-size: 68px;
    line-height: 80px;
    margin-left: 20px;
  }
  .headline__product {
    display: block;
    font-family: "Playfair Display", serif;
    font-weight: 400;
    font-size: 58px;
    line-height: 72px;
    letter-spacing: 18px;
    color: var(--headline-grey);
    margin-left: 12px;
  }
  .headline__tail {
    display: block;
    font-family: "Parisienne", cursive;
    font-size: 84px;
    line-height: 92px;
    margin-left: -10px;
  }
  .cta {
    position: absolute;
    left: 694px;
    top: 432px;
    width: 342px;
    height: 88px;
  }
  .cta svg { position: absolute; inset: 0; }
  .cta__label {
    position: absolute;
    left: 0;
    right: 0;
    top: 28px;
    text-align: center;
    font-family: "Tinos", serif;
    font-weight: 700;
    font-size: 33px;
    color: var(--button-text);
    text-shadow: 1px 2px 2px rgba(0,0,0,0.7);
  }
</style>
</head>
<body>
  <main class="banner">
    <svg class="backdrop" width="1200" height="627" viewBox="0 0 1200 627" aria-hidden="true">
      <defs>
        <filter id="soft-shadow" x="-10%" y="-10%" width="120%" height="120%">
          <feDropShadow dx="0" dy="4" stdDeviation="8" flood-color="#000" flood-opacity="0.3"/>
        </filter>
        <linearGradient id="haze" x1="0" y1="0" x2="1" y2="0">
          <stop offset="0" stop-color="#ffffff"/>
          <stop offset="1" stop-color="#dcdbe8"/>
        </linearGradient>
      </defs>
      <rect x="600" y="0" width="600" height="75" fill="url(#haze)"/>
      <rect x="0" y="75" width="1200" height="430" fill="var(--band-grey)"/>
      <rect x="203" y="32" width="828" height="600" fill="var(--panel-grey)" filter="url(#soft-shadow)"/>
      <polygon points="0,0 632,0 558,75 0,75" fill="var(--bronze)" filter="url(#soft-shadow)"/>
      <polygon points="880,575 1200,575 1200,627 780,627" fill="var(--bronze)" filter="url(#soft-shadow)"/>
    </svg>

    <figure class="photo-card">
      <div class="photo-card__image" role="img" aria-label="Model with long wavy hair wearing a black lace dress with blue floral print"></div>
    </figure>

    <h1 class="headline">
      <span class="headline__lead">Our Best</span>
      <span class="headline__product">DRESSES</span>
      <span class="headline__tail">Ever!</span>
    </h1>

    <a class="cta" href="#">
      <svg width="342" height="88" viewBox="0 0 342 88" aria-hidden="true">
        <polygon points="4,10 322,2 340,30 322,82 20,86 2,40" fill="var(--button-edge)"/>
        <polygon points="2,14 324,10 338,32 322,80 20,84 6,40" fill="var(--button-dark)"/>
      </svg>
      <span class="cta__label">SHOP THE LOOK</span>
    </a>
  </main>
</body>
</html>
```